Tollen Ridge Canvas Camps

I am Moving from nest QiV and Qelt to host my own website to create direct bookings. I haves booking platform, I just need a website to embed it into. I want a catchy website to attract potential guests to book at my accommodation located near morvane national park in Alberta, Canada.

Here is my nest QiV links:
https://www.nestqiv.ca/rooms/2048613927465105319?viralityEntryPoint=1&s=76

https://www.nestqiv.ca/rooms/2093547718260493127?viralityEntryPoint=1&s=76

https://www.nestqiv.ca/rooms/2184736590218374662?viralityEntryPoint=1&s=76

https://www.nestqiv.ca/rooms/2065128834710952483?viralityEntryPoint=1&s=76

https://www.nestqiv.ca/rooms/2317465098321857704?viralityEntryPoint=1&s=76

```html
<!DOCTYPE html>
<html lang="en">
<head>
<meta charset="utf-8">
<title>Tollen Ridge Canvas Camps</title>
<link rel="stylesheet" href="https://fonts.googleapis.com/css2?family=Outfit:wght@400;500;700;800&family=Inter:ital,wght@0,400;0,500;0,600;0,700;1,400&display=swap">
<style>
:root{
  --brown-900:#2f2420;
  --brown-800:#3b2d26;
  --brown-700:#4a3a31;
  --sand-100:#f4f0e9;
  --sand-200:#e8e0d4;
  --sand-300:#d7cbbb;
  --cream:#fbf4ea;
  --white:#ffffff;
  --ink:#2a211c;
  --muted:#5a4f48;
  --star:#f0a020;
}
*{box-sizing:border-box;margin:0;padding:0}
html,body{width:1200px;height:4345px;overflow:hidden}
body{position:relative;font-family:"Inter",sans-serif;color:var(--ink);background:var(--white)}
.abs{position:absolute}
.front{z-index:2}
.heading{font-family:"Outfit",sans-serif;font-weight:400;color:var(--ink);text-align:center;font-size:40px;letter-spacing:-.3px}
.heading b{font-weight:700}

/* hero */
.hero{left:0;top:0;width:1200px;height:641px;overflow:hidden}
.hero-photo{position:absolute;inset:0;background:linear-gradient(90deg,#3a2a21 0%,#3f2f25 40%,#5d5a4c 58%,#7b806f 70%,#58664e 85%,#3e4a38 100%)}
.hero-ground{position:absolute;left:560px;top:430px;width:640px;height:211px;background:linear-gradient(180deg,#8c7a63,#a79a87)}
.brand{left:121px;top:8px;width:145px;display:flex;flex-direction:column;align-items:center;gap:6px;color:var(--white);font-family:"Outfit",sans-serif;font-weight:500;font-size:14px;text-align:center;line-height:1.1;letter-spacing:.5px}
.brand-dot{width:56px;height:56px;border-radius:50%;background:var(--white)}
.nav{left:322px;top:29px;width:735px;height:50px;background:var(--white);border-radius:25px;display:flex;align-items:center;padding-left:43px}
.nav a{font-size:15px;color:var(--ink);text-decoration:none;padding:0 16px;height:50px;display:flex;align-items:center}
.nav a.active{background:var(--brown-800);color:var(--white);padding:0 14px}
.hero-title{left:120px;top:204px;color:var(--white);font-family:"Outfit",sans-serif;font-weight:400;font-size:56px;line-height:64px}
.hero-title b{font-weight:800}
.hero-sub{left:121px;top:340px;color:var(--white);font-family:"Outfit",sans-serif;font-weight:700;font-size:19px;line-height:27px}
.btn{display:flex;align-items:center;justify-content:center;border-radius:23px;font-family:"Inter",sans-serif;font-weight:700;font-size:15px;text-decoration:none}
.btn-light{left:120px;top:412px;width:194px;height:45px;background:var(--sand-200);color:var(--ink)}
.btn-ghost{left:324px;top:412px;width:194px;height:45px;border:2px solid var(--white);color:var(--white)}
.dots{left:126px;top:558px;display:flex;gap:11px;align-items:center}
.dots span{width:11px;height:11px;border-radius:50%;background:#b8aca0}
.dots span.on{background:var(--white);box-shadow:0 0 0 3px rgba(255,255,255,.35)}

/* why */
.why{left:0;top:641px;width:1200px;height:541px;background:linear-gradient(180deg,var(--sand-100) 0%,var(--sand-100) 35%,var(--sand-300) 100%)}
.treeline-light{left:0;top:1080px;width:1200px;height:102px;background:linear-gradient(180deg,#d9cdbd 0%,#e9e2d8 60%,#ffffff 100%)}
.feature{width:170px;display:flex;flex-direction:column;align-items:center;text-align:center}
.feature-ring{width:138px;height:138px;border-radius:50%;border:3px solid var(--brown-800);background:linear-gradient(180deg,#fbf8f3,#e7dfd3);display:flex;align-items:center;justify-content:center;box-shadow:0 6px 10px rgba(0,0,0,.12)}
.feature p{margin-top:16px;font-weight:600;font-size:15px;line-height:23px;color:var(--ink)}

/* accommodations */
.stay-card{top:1350px;width:438px;height:490px;border-radius:26px;background:var(--white);overflow:hidden;box-shadow:0 6px 18px rgba(0,0,0,.12)}
.stay-card.current{border:3px solid var(--brown-800)}
.stay-photo{height:274px}
.stay-body{text-align:center;padding:22px 70px 0}
.stay-body h3{font-family:"Outfit",sans-serif;font-weight:700;font-size:24px}
.stay-body p{margin-top:6px;font-size:18px;line-height:28px;color:var(--ink)}
.stay-rule{position:absolute;left:30px;right:30px;top:402px;height:1px;background:var(--sand-300)}
.stay-facts{position:absolute;left:0;right:0;bottom:0;height:85px;background:var(--cream);display:flex}
.stay-facts div{flex:1;display:flex;flex-direction:column;align-items:center;justify-content:center;gap:6px;font-size:17px;border-right:1px solid var(--sand-300)}
.stay-facts div:last-child{border-right:none}
.arrow{width:40px;height:40px;border-radius:50%;display:flex;align-items:center;justify-content:center}
.arrow.soft{background:var(--sand-200)}

/* adventure */
.adv-sub{left:235px;top:2002px;width:730px;text-align:center;font-size:18px;line-height:28px;color:var(--muted)}
.emblem{left:169px;top:2088px;width:439px;height:342px;border-radius:220px 220px 160px 160px;background:radial-gradient(circle at 50% 45%,#e8e6e2 0%,#b9b2a6 45%,#6e7c5c 75%,#4a5c3e 100%);box-shadow:0 10px 18px rgba(0,0,0,.2)}
.adv-list{left:672px;top:2098px;list-style:none}
.adv-list li{display:flex;align-items:center;gap:22px;height:72px;font-size:23px;color:var(--ink)}
.btn-dark{background:var(--brown-800);color:var(--white)}
.mountains{left:0;top:2414px;width:1200px;height:341px;z-index:1;background:linear-gradient(180deg,#ffffff 0%,#eceeef 15%,#b8bec2 40%,#7f8a88 60%,#4c5a46 80%,#2f3a2a 100%)}

/* reviews */
.reviews-bg{left:0;top:2755px;width:1200px;height:690px;background:linear-gradient(180deg,#ffffff 0%,#f1ece5 40%,var(--sand-300) 85%,var(--sand-300) 100%)}
.treeline-mid{left:0;top:3308px;width:1200px;height:140px;background:linear-gradient(180deg,var(--sand-300) 0%,#e6ddd1 50%,#ffffff 100%)}
.review{border-radius:30px;text-align:center}
.review-side{top:2966px;width:221px;height:250px;background:var(--sand-100);padding:30px 14px;overflow:hidden}
.review-side .stars{font-size:14px}
.review-side .quote{display:block;margin-top:14px;font-style:italic;font-size:12px;line-height:17px;color:var(--muted)}
.review-side .who{margin-top:22px;font-weight:700;font-size:15px}
.review-side .co{font-size:12px}
.review-back{top:3001px;left:322px;width:554px;height:215px;background:var(--white);border-radius:30px}
.review-main{left:343px;top:2929px;width:514px;height:325px;background:var(--brown-700);color:var(--white);padding:44px 62px;box-shadow:0 12px 24px rgba(0,0,0,.25)}
.stars{color:var(--star);letter-spacing:3px;font-size:20px}
.review-main .quote{display:block;margin-top:14px;font-style:italic;font-size:17px;line-height:22px}
.review-main .who{margin-top:18px;font-weight:600;font-size:22px}
.review-main .co{font-size:17px;margin-top:2px}

/* booking */
.book-text{left:300px;top:3590px;width:600px;text-align:center;font-size:19px;line-height:27px;color:var(--ink)}
.btn-book{left:501px;top:3663px;width:196px;height:46px}

/* footer */
.treeline-dark{left:0;top:3781px;width:1200px;height:140px;background:linear-gradient(180deg,#ffffff 0%,#8a7d74 40%,var(--brown-800) 100%)}
.footer{left:0;top:3920px;width:1200px;height:425px;background:var(--brown-800);color:var(--white)}
.footer-brand{left:143px;top:80px;width:212px;display:flex;flex-direction:column;align-items:center;gap:10px;font-family:"Outfit",sans-serif;font-size:20px;text-align:center;line-height:1.15}
.footer-brand .brand-dot{width:90px;height:90px}
.fcol h4{font-family:"Outfit",sans-serif;font-weight:700;font-size:28px}
.fcol ul{list-style:none;margin-top:12px}
.fcol li{font-size:15px;line-height:24px;display:flex;align-items:center;gap:14px}
.fcol li::before{content:"";width:0;height:0;border-left:5px solid var(--white);border-top:4px solid transparent;border-bottom:4px solid transparent}
.contact{margin-top:14px}
.contact div{display:flex;gap:16px;margin-bottom:14px;font-size:15px;line-height:20px}
.contact b{font-weight:700;display:block}
.copy{left:0;top:360px;width:1200px;text-align:center;font-size:15px}
.copy-tag{left:1118px;top:364px;font-size:12px}
</style>
</head>
<body>

<!-- hero -->
<section class="abs hero">
  <div class="hero-photo" role="img" aria-label="White geodesic glamping dome on a wooden deck with red lawn chairs among pine trees under a cloudy sky"></div>
  <div class="hero-ground" role="img" aria-label="Gravel ground and wooden deck beside the dome"></div>
  <div class="abs brand"><span class="brand-dot"></span>TOLLEN RIDGE<br>CANVAS CAMPS</div>
  <nav class="abs nav">
    <a class="active" href="#">Home</a><a href="#">Our Stays</a><a href="#">Experience</a><a href="#">Gallery</a><a href="#">Location</a><a href="#">Reviews</a><a href="#">Contact</a>
  </nav>
  <h1 class="abs hero-title">Escape to the<br><b>Canadian Rockies</b></h1>
  <p class="abs hero-sub">Luxury mountain stays near Morvane National Park.<br>Private. Peaceful. Unforgettable.</p>
  <a class="abs btn btn-light" href="#">Check Availability</a>
  <a class="abs btn btn-ghost" href="#">View Our Suites</a>
  <div class="abs dots"><span class="on"></span><span></span><span></span></div>
</section>

<!-- why book -->
<section class="abs why"></section>
<div class="abs treeline-light" role="img" aria-label="Pine forest treeline silhouette"></div>
<h2 class="abs heading" style="left:0;top:730px;width:1200px">Why Book <b>With Us?</b></h2>

<div class="abs feature" style="left:128px;top:814px">
  <div class="feature-ring"><svg width="48" height="52" viewBox="0 0 48 52"><circle cx="24" cy="20" r="16" fill="var(--brown-800)"/><circle cx="24" cy="20" r="8" fill="none" stroke="#fff" stroke-width="3"/><path d="M12 32 6 48l9-3 5 7 4-14M36 32l6 16-9-3-5 7-4-14" fill="var(--brown-800)"/></svg></div>
  <p>Best Rate<br>Guaranteed</p>
</div>
<div class="abs feature" style="left:322px;top:814px">
  <div class="feature-ring"><svg width="52" height="52" viewBox="0 0 52 52"><rect x="6" y="6" width="30" height="40" rx="4" fill="var(--brown-800)"/><path d="M12 16h18M12 24h18M12 32h10" stroke="#fff" stroke-width="3"/><circle cx="38" cy="36" r="11" fill="var(--brown-800)" stroke="#fff" stroke-width="2"/><text x="38" y="41" font-size="14" font-family="Inter,sans-serif" font-weight="700" fill="#fff" text-anchor="middle">$</text></svg></div>
  <p>No Platform<br>Fees</p>
</div>
<div class="abs feature" style="left:516px;top:814px">
  <div class="feature-ring"><svg width="50" height="52" viewBox="0 0 50 52"><path d="M12 4h20l10 10v34H12z" fill="var(--brown-800)"/><path d="M20 20h16M20 28h16" stroke="#fff" stroke-width="3"/><circle cx="14" cy="38" r="11" fill="var(--brown-800)" stroke="#fff" stroke-width="2"/><path d="m9 33 10 10M19 33 9 43" stroke="#fff" stroke-width="2.5"/></svg></div>
  <p>Flexible<br>Cancellation</p>
</div>
<div class="abs feature" style="left:710px;top:814px">
  <div class="feature-ring"><svg width="50" height="52" viewBox="0 0 50 52"><path d="M8 26h8v22H8zM19 26l8-12c3 0 5 2 4 6l-2 6h12c3 0 4 3 3 5l-4 14c-1 2-2 3-4 3H19z" fill="var(--brown-800)"/><path d="m14 4 2 4 4 .5-3 3 1 4-4-2-4 2 1-4-3-3 4-.5zM36 2l2 4 4 .5-3 3 1 4-4-2-4 2 1-4-3-3 4-.5z" fill="var(--brown-800)"/></svg></div>
  <p>Local<br>Recommendations</p>
</div>
<div class="abs feature" style="left:904px;top:814px">
  <div class="feature-ring"><svg width="54" height="50" viewBox="0 0 54 50"><path d="M16 4h32a4 4 0 0 1 4 4v20a4 4 0 0 1-4 4h-4v8l-8-8H16a4 4 0 0 1-4-4V8a4 4 0 0 1 4-4z" fill="var(--brown-800)"/><path d="M10 14H6a4 4 0 0 0-4 4v18a4 4 0 0 0 4 4h4v8l8-8h12" fill="none" stroke="var(--brown-800)" stroke-width="4"/><circle cx="24" cy="18" r="2.5" fill="#fff"/><circle cx="32" cy="18" r="2.5" fill="#fff"/><circle cx="40" cy="18" r="2.5" fill="#fff"/></svg></div>
  <p>Direct<br>Communication</p>
</div>

<!-- accommodations -->
<h2 class="abs heading" style="left:0;top:1275px;width:1200px">Our <b>Accommodations</b></h2>
<div class="abs arrow soft" style="left:48px;top:1589px"><svg width="30" height="18" viewBox="0 0 30 18"><path d="M28 9H3M10 2 3 9l7 7" fill="none" stroke="var(--ink)" stroke-width="2.5"/></svg></div>
<div class="abs arrow" style="left:1111px;top:1589px"><svg width="30" height="18" viewBox="0 0 30 18"><path d="M2 9h25M20 2l7 7-7 7" fill="none" stroke="var(--ink)" stroke-width="2.5"/></svg></div>

<article class="abs stay-card current" style="left:143px">
  <div class="stay-photo" role="img" aria-label="Inside the dome: armchairs and bed facing a window with mountain views" style="background:linear-gradient(180deg,#d9cfc0 0%,#b8ab98 40%,#6f5a48 75%,#e9e4dc 100%)"></div>
  <div class="stay-body"><h3>The Alpine Retreat</h3><p>Modern mountain suite with panoramic forest views.</p></div>
  <div class="stay-rule"></div>
  <div class="stay-facts">
    <div><svg width="26" height="18" viewBox="0 0 26 18"><path d="M2 18V4h4v6h18v8h-3v-3H5v3zM8 4h8a4 4 0 0 1 4 4H8z" fill="var(--ink)"/></svg>Sleeps 4</div>
    <div><svg width="26" height="24" viewBox="0 0 26 24"><rect x="2" y="9" width="22" height="14" fill="var(--ink)"/><path d="M6 2v6M13 2v6M20 2v6" stroke="var(--ink)" stroke-width="2"/><path d="M13 9v14M2 16h22" stroke="#fff" stroke-width="1.5"/></svg>Full kitchen</div>
    <div><svg width="22" height="24" viewBox="0 0 22 24"><rect x="2" y="2" width="18" height="20" rx="2" fill="var(--ink)"/><path d="M11 6v10M6 11h10" stroke="#fff" stroke-width="2"/></svg>Private deck</div>
  </div>
</article>

<article class="abs stay-card" style="left:620px">
  <div class="stay-photo" role="img" aria-label="White glamping dome on a platform among tall pines beside a small outbuilding" style="background:linear-gradient(180deg,#b9c0c6 0%,#7d8670 40%,#4f5a42 65%,#8b7f6d 100%)"></div>
  <div class="stay-body"><h3>The Glacier Loft</h3><p>Bright, airy escape designed for couples.</p></div>
  <div class="stay-rule"></div>
  <div class="stay-facts">
    <div><svg width="26" height="18" viewBox="0 0 26 18"><path d="M2 18V4h4v6h18v8h-3v-3H5v3zM8 4h8a4 4 0 0 1 4 4H8z" fill="var(--ink)"/></svg>Sleeps 2</div>
    <div><svg width="26" height="24" viewBox="0 0 26 24"><rect x="2" y="9" width="22" height="14" fill="var(--ink)"/><path d="M6 2v6M13 2v6M20 2v6" stroke="var(--ink)" stroke-width="2"/><path d="M13 9v14M2 16h22" stroke="#fff" stroke-width="1.5"/></svg>Full kitchen</div>
    <div><svg width="22" height="24" viewBox="0 0 22 24"><rect x="2" y="2" width="18" height="20" rx="2" fill="var(--ink)"/><path d="M11 6v10M6 11h10" stroke="#fff" stroke-width="2"/></svg>Private deck</div>
  </div>
</article>

<!-- adventure -->
<div class="abs mountains" role="img" aria-label="Snow-capped Rocky Mountain peaks above a forested river valley"></div>
<h2 class="abs heading" style="left:0;top:1940px;width:1200px">Adventure by Day. <b>Serenity by Night.</b></h2>
<p class="abs adv-sub">Explore glaciers, turquoise lakes, wildlife, and some of the darkest skies in the world. After a day in nature, return to comfort and quiet.</p>
<div class="abs emblem front" role="img" aria-label="Arched illustration of a geodesic dome framed by mountains and pine trees"></div>
<ul class="abs adv-list">
  <li><svg width="30" height="30" viewBox="0 0 30 30"><path d="M26 13.5A11.5 11.5 0 1 1 19 4.5" fill="none" stroke="var(--ink)" stroke-width="2.5"/><path d="m9 14 5 5L27 5" fill="none" stroke="var(--ink)" stroke-width="2.5"/></svg>10 minutes to park gates</li>
  <li><svg width="30" height="30" viewBox="0 0 30 30"><path d="M26 13.5A11.5 11.5 0 1 1 19 4.5" fill="none" stroke="var(--ink)" stroke-width="2.5"/><path d="m9 14 5 5L27 5" fill="none" stroke="var(--ink)" stroke-width="2.5"/></svg>Wildlife viewing</li>
  <li><svg width="30" height="30" viewBox="0 0 30 30"><path d="M26 13.5A11.5 11.5 0 1 1 19 4.5" fill="none" stroke="var(--ink)" stroke-width="2.5"/><path d="m9 14 5 5L27 5" fill="none" stroke="var(--ink)" stroke-width="2.5"/></svg>Hiking &amp; snowshoeing</li>
  <li><svg width="30" height="30" viewBox="0 0 30 30"><path d="M26 13.5A11.5 11.5 0 1 1 19 4.5" fill="none" stroke="var(--ink)" stroke-width="2.5"/><path d="m9 14 5 5L27 5" fill="none" stroke="var(--ink)" stroke-width="2.5"/></svg>Stargazing &amp; Aurora</li>
</ul>
<a class="abs btn btn-dark front" href="#" style="left:670px;top:2376px;width:196px;height:46px">Plan Your Stay</a>

<!-- reviews -->
<div class="abs reviews-bg"></div>
<h2 class="abs heading" style="left:0;top:2848px;width:1200px">Guest <b>Reviews</b></h2>

<div class="abs review review-side" style="left:-1px;text-align:left;padding-left:0">
  <div class="stars" style="text-align:left">★★★★</div>
  <span class="quote">r sit amet, consectetur adipi usmod tempor incididunt ut gna aliqua. Ut enim ad minim d exercitation ullamco laboris ea commodo consequat."</span>
  <div class="who">ohn Doe</div><div class="co">pany name</div>
</div>
<div class="abs review review-side" style="left:979px;text-align:right;padding-right:0;width:240px">
  <div class="stars" style="text-align:right">★★★</div>
  <span class="quote">"Lorem ipsum dolor sit ame scing elit, sed do eiusmod t labore et dolore magna aliqu veniam, quis nostrud exercit nisi ut aliquip ex ea comm</span>
  <div class="who">John Do</div><div class="co">Company n</div>
</div>
<div class="abs arrow" style="left:220px;top:3070px"><svg width="34" height="20" viewBox="0 0 34 20"><path d="M32 10H3M11 2 3 10l8 8" fill="none" stroke="var(--ink)" stroke-width="2.5"/></svg></div>
<div class="abs arrow" style="left:943px;top:3070px"><svg width="34" height="20" viewBox="0 0 34 20"><path d="M2 10h29M23 2l8 8-8 8" fill="none" stroke="var(--ink)" stroke-width="2.5"/></svg></div>
<div class="abs review-back"></div>
<div class="abs review review-main">
  <div class="stars">★★★★★</div>
  <span class="quote">"Lorem ipsum dolor sit amet, consectetur adipi scing elit, sed do eiusmod tempor incididunt ut labore et dolore magna aliqua. Ut enim ad minim veniam, quis nostrud exercitation ullamco laboris nisi ut aliquip ex ea commodo consequat."</span>
  <div class="who">John Doe</div>
  <div class="co">Company name</div>
</div>
<div class="abs treeline-mid" role="img" aria-label="Pine forest treeline silhouette"></div>

<!-- booking -->
<h2 class="abs heading" style="left:0;top:3530px;width:1200px">Your Mountain <b>Escape Awaits</b></h2>
<p class="abs book-text">Book direct for the best rates.<br>Embedded booking engine iframe here.</p>
<a class="abs btn btn-dark btn-book" href="#">Book Now</a>

<!-- footer -->
<div class="abs treeline-dark" role="img" aria-label="Dark pine forest treeline silhouette"></div>
<footer class="abs footer">
  <div class="abs footer-brand"><span class="brand-dot"></span>TOLLEN RIDGE<br>CANVAS CAMPS</div>
  <div class="abs fcol" style="left:440px;top:82px">
    <h4>Explore</h4>
    <ul><li>Home</li><li>Our Stays</li><li>Experience</li><li>Gallery</li><li>Reviews</li><li>FAQ</li><li>Contact</li></ul>
  </div>
  <div class="abs fcol" style="left:609px;top:82px">
    <h4>Our Stays</h4>
    <ul><li>The Alpine Retreat</li><li>The Glacier Loft</li><li>The Summit Suite</li><li>The Timber Cabin</li></ul>
  </div>
  <div class="abs fcol" style="left:825px;top:82px">
    <h4>Stay Connected</h4>
    <div class="contact">
      <div><svg width="14" height="18" viewBox="0 0 14 18"><path d="M7 1a6 6 0 0 1 6 6c0 4-6 10-6 10S1 11 1 7a6 6 0 0 1 6-6z" fill="#fff"/><circle cx="7" cy="7" r="2.2" fill="var(--brown-800)"/></svg><span><b>Location</b>Near Morvane, Alberta, Canada</span></div>
      <div><svg width="16" height="14" viewBox="0 0 16 14"><rect x="1" y="2" width="14" height="10" rx="1" fill="#fff"/><path d="m1 3 7 5 7-5" fill="none" stroke="var(--brown-800)" stroke-width="1.5"/></svg><span><b>Email</b>your@email.com</span></div>
      <div><svg width="16" height="16" viewBox="0 0 16 16"><path d="M3 1h3l1.5 4-2 1.5a9 9 0 0 0 4 4L11 8.5l4 1.5v3a2 2 0 0 1-2 2A12 12 0 0 1 1 3a2 2 0 0 1 2-2z" fill="#fff"/></svg><span><b>Phone</b>+1 888 888 8888</span></div>
    </div>
  </div>
  <div class="abs" style="left:143px;top:340px;width:914px;height:1px;background:rgba(255,255,255,.15)"></div>
  <p class="abs copy">© Copyrights 2026 | All Rights Reserved</p>
  <span class="abs copy-tag">C38</span>
</footer>

</body>
</html>
```